Redo a PPT pres. - Real Estate in Brazil - Socially equitable investments in Social Housing

We need to redo the presentation attached. It is an institutional presentation to attract local and foreign investors to invest in Brazilian Social Housing Projects structured by our company "TLR".
A middle class of 100 million, a housing deficit of 9M, a strong political will & positive income generation trends constitute grounds for a significant demand in social housing.
This make a perfect scheme for investors to invest in Brazilian Social Housing.
"TLR", is a consulting "boutique" focused in Brazilian real estate, specialized in structuring, analyzing and originating Brazilian social housing projects.
TLR is part of the group TLB. TLB is structured to create value through each step of the residential real estate business - structuring, financing, sales, marketing and technology.
We would like to see designs that use mainly the color blue. The final design should communicate financial safety and professionalism. In order to reach our needs, the designer will need to have basic understanding of finance and investment in order to highlight the most important information.
The idea is to receive back the PPT with each page redesigned and an homogeneous identity.
To all designers,
Target Market(s)
Institutional Investors and wealthy individuals
Industry/Entity Type
Residential
Look and feel

```html
<!DOCTYPE html>
<html lang="en">
<head>
<meta charset="utf-8">
<title>Social Housing in Brazil – TLR</title>
<link rel="stylesheet" href="https://fonts.googleapis.com/css2?family=Open+Sans:wght@400;600;700;800&display=swap">
<style>
:root{
  --stage:#000;
  --navy:#17223d;
  --navy-deep:#0f1830;
  --blue:#3b5087;
  --blue-mid:#5b73a8;
  --sky:#8fa6cc;
  --green:#8cc63f;
  --green-dark:#6aa52a;
  --white:#fff;
  --ink:#3a3f4b;
  --muted:#8b909a;
  --rule:#d9dde4;
}
*{box-sizing:border-box;margin:0;padding:0}
html,body{width:768px;height:1200px;overflow:hidden;background:var(--stage)}
body{position:relative;font-family:"Open Sans",Arial,sans-serif;color:var(--ink)}
.slide{position:absolute;width:366px;height:268px;overflow:hidden;background:var(--white)}
.col-l{left:8px}.col-r{left:394px}
.row-1{top:25px}.row-2{top:313px}.row-3{top:601px}.row-4{top:889px}

.city{position:absolute;background:linear-gradient(170deg,#6f87b3 0%,#3e578a 40%,#22345d 75%,#1a2746 100%)}
.city.full{inset:0}
.city.half{left:0;top:0;width:165px;height:268px}
.city::after{content:"";position:absolute;inset:0;background:linear-gradient(180deg,rgba(23,34,61,.15),rgba(23,34,61,.55))}

.tab{position:absolute;left:14px;top:0;width:46px;height:44px}
.tab svg{position:absolute;inset:0}
.brand{position:absolute;left:0;right:0;top:14px;display:flex;align-items:center;justify-content:center;gap:2px;color:var(--white);font-weight:700;font-size:10px;letter-spacing:.5px}
.brand i{display:block;width:4px;height:4px;background:var(--white)}

.side-title{position:absolute;left:12px;width:141px;color:var(--white);font-weight:800;font-size:11px;line-height:1.2;text-transform:uppercase}
.side-bar{position:absolute;left:0;width:165px;height:20px;bottom:12px;background:var(--green-dark);color:var(--white);font-size:5px;line-height:1.3;padding:3px 8px;display:flex;align-items:center}
.pager{position:absolute;right:10px;bottom:6px;font-size:6px;color:var(--muted);letter-spacing:1px}
.pager b{color:var(--blue);font-weight:700}

.light{position:absolute;border-radius:50%;display:flex;align-items:center;justify-content:center;font-weight:600}
.light.solid{border:3px solid rgba(255,255,255,.85);background:rgba(140,198,63,.55);color:var(--white)}
.light.plain{background:var(--white);border:3px solid rgba(255,255,255,.5);box-shadow:0 0 0 2px rgba(255,255,255,.35);color:var(--green-dark)}

/* cover */
.cover-banner{position:absolute;left:92px;top:0;width:186px;height:212px}
.cover-banner svg{position:absolute;inset:0}
.cover-title{position:absolute;left:0;right:0;top:60px;text-align:center;color:var(--white);font-weight:800;font-size:15px;line-height:1.15;letter-spacing:.5px}
.cover-sub{position:absolute;left:14px;right:14px;top:112px;text-align:center;color:var(--green);font-size:7px;line-height:1.35;letter-spacing:.5px}
.cover-logo{position:absolute;left:62px;top:146px;width:62px;height:20px;background:var(--white);color:var(--navy);font-weight:700;font-size:9px;display:flex;align-items:center;justify-content:center;gap:2px}
.cover-logo i{display:block;width:4px;height:4px;background:var(--navy)}

/* wheel */
.wheel{position:absolute;left:182px;top:14px;width:172px;height:212px}
.node{position:absolute;width:50px;height:50px;margin:-25px 0 0 -25px;border-radius:50%;border:1.5px solid var(--green);background:var(--white);display:flex;align-items:center;justify-content:center;text-align:center;font-size:4.3px;line-height:1.3;padding:5px;color:var(--ink)}
.node.alt{border-color:var(--green-dark)}

/* agenda */
.agenda{position:absolute;left:182px;top:26px;width:170px;list-style:none}
.agenda li{display:flex;gap:7px;align-items:flex-start;margin-bottom:8px;font-size:5.5px;line-height:1.35}
.agenda .num{flex:none;width:14px;height:13px;background:var(--green);color:var(--white);font-weight:700;font-size:6.5px;display:flex;align-items:center;justify-content:center}
.agenda strong{display:block;font-size:6px;color:var(--navy)}

/* content panels */
.panel{position:absolute;left:178px;right:12px}
.bar-head{background:var(--blue);color:var(--white);font-weight:700;font-size:6px;padding:3px 6px;letter-spacing:.4px}
.copy{font-size:4.4px;line-height:1.45;color:var(--ink);padding:4px 2px}
.copy p{margin-bottom:2px}
.copy ul{list-style:none;padding-left:0}
.copy li{position:relative;padding-left:5px;margin-bottom:1.5px}
.copy li::before{content:"";position:absolute;left:0;top:1.8px;width:2px;height:2px;background:var(--blue)}
.copy .note{color:var(--muted);display:block}
.copy b{color:var(--navy)}
.tri{display:block;margin:4px auto}
.chart-box{border:1px solid var(--rule);padding:3px}

/* track record */
.track{position:absolute;left:178px;right:12px;top:10px}
.block{display:flex;margin-top:5px}
.block-main{flex:1}
.block-head{background:var(--green);color:var(--white);font-weight:700;font-size:6.5px;padding:3px 6px}
.block-body{display:flex;background:#f3f5f8;padding:3px;gap:3px}
.block-body ul{flex:1;list-style:none;font-size:3.8px;line-height:1.5}
.rates{flex:1.3;border-collapse:collapse;font-size:3.6px}
.rates th{background:var(--blue);color:var(--white);text-align:left;padding:1px 2px}
.rates td{border-bottom:1px solid var(--rule);padding:.8px 2px}
.block-side{width:30px;display:flex;align-items:center;justify-content:center}
.track-foot{font-size:4.2px;line-height:1.45;margin-top:6px}
</style>
</head>
<body>

<!-- 1 cover -->
<section class="slide col-l row-1">
  <div class="city full" role="img" aria-label="Skyline of a dense high-rise city at dusk in blue tones"></div>
  <div class="cover-banner">
    <svg viewBox="0 0 186 212" preserveAspectRatio="none"><polygon points="0,0 186,0 186,212 93,190 0,212" fill="#17223d" fill-opacity=".92"/></svg>
    <h1 class="cover-title">SOCIAL HOUSING<br>IN BRAZIL</h1>
    <p class="cover-sub">HIGH YIELD RETURN FOR<br>A QUASI SOVEREIGN RISK</p>
    <div class="cover-logo"><i></i>TLR</div>
  </div>
</section>

<!-- 2 how to invest -->
<section class="slide col-r row-1">
  <div class="city half" role="img" aria-label="City skyline photograph in blue tones"></div>
  <div class="tab"><svg viewBox="0 0 46 44"><polygon points="0,0 46,0 46,44 23,36 0,44" fill="#17223d"/></svg><div class="brand"><i></i>TLR</div></div>
  <h2 class="side-title" style="top:112px">How to invest<br>in social housing<br>in Brazil?</h2>
  <div class="side-bar">A socially conscious &amp; lucrative investment</div>
  <div class="wheel">
    <div class="node" style="left:86px;top:28px">Building housing units for low to middle class buyers</div>
    <div class="node alt" style="left:140px;top:56px">Investing in individual projects Management</div>
    <div class="node" style="left:148px;top:112px">Specialized international and local team</div>
    <div class="node alt" style="left:134px;top:166px">Co-investing with local mid-size developers</div>
    <div class="node" style="left:86px;top:188px">Co-financed by government</div>
    <div class="node alt" style="left:36px;top:166px">Equity participation of R$5-10 millions</div>
    <div class="node" style="left:24px;top:112px">Time Horizon 3-4 years</div>
    <div class="node alt" style="left:32px;top:56px">Target IRR 20-30%</div>
  </div>
  <div class="pager">&lt; <b>02</b> &gt;</div>
</section>

<!-- 3 agenda -->
<section class="slide col-l row-2">
  <div class="city half" role="img" aria-label="City skyline photograph in blue tones"></div>
  <div class="tab"><svg viewBox="0 0 46 44"><polygon points="0,0 46,0 46,44 23,36 0,44" fill="#17223d"/></svg><div class="brand"><i></i>TLR</div></div>
  <h2 class="side-title" style="top:128px;text-align:center">The time is now!</h2>
  <ol class="agenda">
    <li><span class="num">1</span><span><strong>Macro-environment &amp; Mortgage market</strong>Green Light</span></li>
    <li><span class="num">2</span><span><strong>A sophisticated &amp; successful program</strong>Catalyst</span></li>
    <li><span class="num">3</span><span><strong>Investment Structure of a typical project</strong>Leverage &amp; Limited Risks</span></li>
    <li><span class="num">4</span><span><strong>Small &amp; mid size developers</strong>A partner by choice</span></li>
    <li><span class="num">5</span><span><strong>TLR</strong>Value added &amp; Risk mitigation</span></li>
    <li><span class="num">6</span><span><strong>TLB</strong>TLR, part of an integrated family of companies</span></li>
    <li><span class="num">7</span><span><strong>Appendix:</strong>Next step… TLR Fund (2013)</span></li>
  </ol>
  <div class="pager">&lt; <b>02</b> &gt;</div>
</section>

<!-- 4 section divider -->
<section class="slide col-r row-2">
  <div class="city full" role="img" aria-label="Harbour city skyline photograph in blue tones"></div>
  <div class="tab"><svg viewBox="0 0 46 44"><polygon points="0,0 46,0 46,44 23,36 0,44" fill="#17223d"/></svg><div class="brand"><i></i>TLR</div></div>
  <div class="light solid" style="left:36px;top:96px;width:84px;height:84px;font-size:9px">Green Light</div>
  <h2 class="side-title" style="left:140px;top:214px;width:210px;text-align:right;font-size:9px">Macro-environment &amp;<br>mortage market</h2>
  <div class="pager" style="color:#c8d2e4">&lt; <b style="color:#fff">03</b> &gt;</div>
</section>

<!-- 5 politics -->
<section class="slide col-l row-3">
  <div class="city half" role="img" aria-label="City skyline photograph in blue tones"></div>
  <div class="tab"><svg viewBox="0 0 46 44"><polygon points="0,0 46,0 46,44 23,36 0,44" fill="#17223d"/></svg><div class="brand"><i></i>TLR</div></div>
  <div class="light plain" style="left:45px;top:70px;width:72px;height:72px;font-size:8px">Green Light</div>
  <h2 class="side-title" style="top:166px">A middle class of<br>100 million people</h2>
  <div class="side-bar">Strong political will &amp; positive income generation trends constitute grounds for a significant demand in social housing</div>
  <div class="panel" style="top:10px">
    <div class="bar-head">POLITICS</div>
    <div class="copy">
      <p>Brazil launched a fierce battle against poverty <b>10 years ago</b> with President Alves. The positive economic environment has helped implement these policies.</p>
      <p><b>Growth Acceleration Program (2007-10): R$500B (*)</b></p>
      <ul><li>Public investments in infrastructure</li><li>Lighten the administrative and legal burden on private initiatives and long-term growth</li><li>Stimulating Credit &amp; Financing for the real estate sector</li></ul>
      <p><b>Growth Acceleration Program (2011-14): R$955B (*)</b></p>
      <ul><li>Better City – A Community: R$60B</li><li>Water, Light, Transportation: R$110B</li><li>Energy: R$460B</li><li>Housing: R$278B – public financing and subsidies through various programs, notably Casa Nova Vida (NLNC) for low and middle classes</li></ul>
    </div>
    <svg class="tri" width="26" height="13" viewBox="0 0 26 13"><polygon points="0,0 26,0 13,13" fill="#8cc63f"/></svg>
    <div class="bar-head">EMERGENCE OF THE MIDDLE CLASS</div>
    <div class="copy">
      <ul>
        <li>It reached remarkable success: poverty has <b>decreased from 28% of population in 1990 to less than 20% in 2012.</b></li>
        <li>More than <b>40M people</b> have recently entered the middle class. They need decent housing.</li>
        <li><b>Middle class will represent 54%</b> of the population by the end of 2012.</li>
        <li>Constitution of an upper middle class with an <b>appetite</b> for pricier products.</li>
        <li>Housing deficit is estimated to be around <b>9M</b>, of which <b>7M</b> in urban housing.</li>
      </ul>
    </div>
  </div>
  <div class="pager">&lt; <b>03</b> &gt;</div>
</section>

<!-- 6 ages chart -->
<section class="slide col-r row-3">
  <div class="city half" role="img" aria-label="City skyline photograph in blue tones"></div>
  <div class="tab"><svg viewBox="0 0 46 44"><polygon points="0,0 46,0 46,44 23,36 0,44" fill="#17223d"/></svg><div class="brand"><i></i>TLR</div></div>
  <div class="light plain" style="left:45px;top:70px;width:72px;height:72px;font-size:8px">Green Light</div>
  <h2 class="side-title" style="top:160px">A middle class of<br>100 million people<br><span style="font-size:9px">and still growing</span></h2>
  <div class="side-bar">Positive demographics &amp; economic environment will sustain the demand</div>
  <div class="panel" style="top:10px">
    <div class="bar-head">Number of people based on ages</div>
    <div class="chart-box">
      <svg width="170" height="118" viewBox="0 0 170 118" font-family="Open Sans, Arial, sans-serif" font-size="4.5" fill="#3a3f4b">
        <g stroke="#e3e6ec" stroke-width=".5"><line x1="30" y1="4" x2="30" y2="94"/><line x1="63" y1="4" x2="63" y2="94"/><line x1="96" y1="4" x2="96" y2="94"/><line x1="129" y1="4" x2="129" y2="94"/><line x1="162" y1="4" x2="162" y2="94"/></g>
        <text x="2" y="14">60-75 years</text><rect x="30" y="8" width="42" height="4" fill="#3b5087"/><rect x="30" y="13" width="70" height="4" fill="#8cc63f"/>
        <text x="2" y="32">40-60 years</text><rect x="30" y="26" width="95" height="4" fill="#3b5087"/><rect x="30" y="31" width="120" height="4" fill="#8cc63f"/>
        <text x="2" y="50">20-40 years</text><rect x="30" y="44" width="124" height="4" fill="#3b5087"/><rect x="30" y="49" width="126" height="4" fill="#8cc63f"/>
        <text x="2" y="68">10-20 years</text><rect x="30" y="62" width="128" height="4" fill="#3b5087"/><rect x="30" y="67" width="116" height="4" fill="#8cc63f"/>
        <text x="2" y="86">0-10 years</text><rect x="30" y="80" width="126" height="4" fill="#3b5087"/><rect x="30" y="85" width="108" height="4" fill="#8cc63f"/>
        <g font-size="4"><text x="28" y="100">0M</text><text x="59" y="100">10M</text><text x="92" y="100">20M</text><text x="125" y="100">30M</text><text x="156" y="100">40M</text></g>
        <rect x="40" y="108" width="6" height="4" fill="#3b5087"/><text x="48" y="112">2000 (176 M)</text>
        <rect x="100" y="108" width="6" height="4" fill="#8cc63f"/><text x="108" y="112">2020 (208 M)</text>
      </svg>
    </div>
    <div class="bar-head" style="margin-top:8px">END BUYERS</div>
    <div class="copy">
      <ul>
        <li>Aging population: Average number of persons per household shrunk from <b>3.7 in 1991 to 3.1 in 2010</b>. Expected to remain around 3.</li>
        <li>Projection of <b>120 more people by 2020</b>.<span class="note">Natural increase in number of households / housing demand</span></li>
        <li>Low and stable unemployment rate: <b>6%</b>.</li>
        <li>Considerable growth in real wages: <b>average 3.5% from 2005-2012</b>.<span class="note">20M more people will have entered Class C from 2008 to 2014</span></li>
      </ul>
    </div>
  </div>
  <div class="pager">&lt; <b>03</b> &gt;</div>
</section>

<!-- 7 wages chart -->
<section class="slide col-l row-4">
  <div class="city half" role="img" aria-label="City skyline photograph in blue tones"></div>
  <div class="tab"><svg viewBox="0 0 46 44"><polygon points="0,0 46,0 46,44 23,36 0,44" fill="#17223d"/></svg><div class="brand"><i></i>TLR</div></div>
  <div class="light plain" style="left:45px;top:70px;width:72px;height:72px;font-size:8px">Green Light</div>
  <h2 class="side-title" style="top:160px">A middle class of<br>100 million people<br><span style="font-size:9px">and still growing</span></h2>
  <div class="side-bar">Positive demographics &amp; economic environment will sustain the demand</div>
  <div class="panel" style="top:10px">
    <div class="bar-head">Number of people based on ages</div>
    <div class="chart-box">
      <svg width="170" height="118" viewBox="0 0 170 118" font-family="Open Sans, Arial, sans-serif" font-size="4.5" fill="#3a3f4b">
        <g stroke="#e3e6ec" stroke-width=".5"><line x1="22" y1="8" x2="166" y2="8"/><line x1="22" y1="28" x2="166" y2="28"/><line x1="22" y1="48" x2="166" y2="48"/><line x1="22" y1="68" x2="166" y2="68"/><line x1="22" y1="88" x2="166" y2="88"/></g>
        <g font-size="4"><text x="8" y="10">10%</text><text x="10" y="30">8%</text><text x="10" y="50">6%</text><text x="10" y="70">4%</text><text x="10" y="90">2%</text></g>
        <g fill="#3b5087">
          <rect x="30" y="48" width="8" height="40"/><rect x="47" y="38" width="8" height="50"/><rect x="64" y="40" width="8" height="48"/><rect x="81" y="42" width="8" height="46"/><rect x="98" y="44" width="8" height="44"/><rect x="115" y="34" width="8" height="54"/><rect x="132" y="60" width="8" height="28"/><rect x="149" y="46" width="8" height="42"/>
        </g>
        <polyline points="34,16 51,20 68,24 85,22 102,30 119,34 136,40 153,40" fill="none" stroke="#8cc63f" stroke-width="2.4"/>
        <g font-size="4"><text x="28" y="96">2005</text><text x="45" y="96">2006</text><text x="62" y="96">2007</text><text x="79" y="96">2008</text><text x="96" y="96">2009</text><text x="113" y="96">2010</text><text x="130" y="96">2011</text><text x="147" y="96">2012</text></g>
        <rect x="36" y="108" width="6" height="4" fill="#3b5087"/><text x="44" y="112">Real Wages Growth</text>
        <rect x="100" y="108" width="6" height="4" fill="#8cc63f"/><text x="108" y="112">Unemployment Rate</text>
      </svg>
    </div>
    <div class="bar-head" style="margin-top:8px">END BUYERS</div>
    <div class="copy">
      <ul>
        <li>Aging population: Average number of persons per household shrunk from <b>3.7 in 1991 to 3.1 in 2010</b>. Expected to remain around 3.</li>
        <li>Projection of <b>120 more people by 2020</b>.<span class="note">Natural increase in number of households / housing demand</span></li>
        <li>Low and stable unemployment rate: <b>6%</b>.</li>
        <li>Considerable growth in real wages: <b>average 3.5% from 2005-2012</b>.<span class="note">20M more people will have entered Class C from 2008 to 2014</span></li>
      </ul>
    </div>
  </div>
  <div class="pager">&lt; <b>03</b> &gt;</div>
</section>

<!-- 8 track record -->
<section class="slide col-r row-4">
  <div class="city half" role="img" aria-label="City skyline photograph in blue tones"></div>
  <div class="tab"><svg viewBox="0 0 46 44"><polygon points="0,0 46,0 46,44 23,36 0,44" fill="#17223d"/></svg><div class="brand"><i></i>TLR</div></div>
  <h2 class="side-title" style="top:150px">NLNC: An impressive<br>track record</h2>
  <div class="side-bar">Major component of the federal efforts on housing NLNC already closes outstanding results in less than 4 years, calling for its extension</div>
  <div class="track">
    <div class="bar-head">IMPRESSIVE TRACK RECORD</div>
    <div class="block">
      <div class="block-main">
        <div class="block-head">NLNC1 (2009-10)</div>
        <div class="block-body">
          <ul><li>Budget of R$34B</li><li>Reached target of 1M units in less than 2 yrs</li><li>Total sales value of R$51B</li></ul>
          <table class="rates"><tr><th>MONTHLY WAGE</th><th>AMOUNT</th></tr><tr><td>Wages of 0-3</td><td>40% / 400k</td></tr><tr><td>Wages of 3-6</td><td>40% / 400k</td></tr><tr><td>Wages of 6-10</td><td>20% / 200k</td></tr></table>
        </div>
      </div>
      <div class="block-side"><svg width="22" height="11" viewBox="0 0 22 11"><polygon points="0,0 22,0 11,11" fill="#8cc63f"/></svg></div>
    </div>
    <div class="block">
      <div class="block-main">
        <div class="block-head">NLNC1 (2011-14)</div>
        <div class="block-body">
          <ul><li>Budget of R$125B</li><li>Reached target of 2M units in less than 3 yrs</li><li>Total sales value of R$160B</li></ul>
          <table class="rates"><tr><th>MONTHLY WAGE</th><th>AMOUNT</th></tr><tr><td>Wages of 0-3</td><td>60% / 1.2M</td></tr><tr><td>Wages of 3-6</td><td>30% / 600k</td></tr><tr><td>Wages of 6-10</td><td>10% / 200k</td></tr></table>
        </div>
      </div>
      <div class="block-side"><svg width="22" height="11" viewBox="0 0 22 11"><polygon points="0,0 22,0 11,11" fill="#8cc63f"/></svg></div>
    </div>
    <div class="block">
      <div class="block-main" style="flex:none;width:70px">
        <div class="block-head">NLNC1 (2015)</div>
        <div class="block-body" style="font-size:4px;height:20px;align-items:center">? ? ? ?</div>
      </div>
    </div>
    <p class="track-foot">After the success of NLNC1 in 2009-10, the Brazilian government approved its continuation, and even doubled both the budget and targets. Surpassing initial projections, NLNC 2011-14 will most likely reach its targets before the deadline. We then expect it to be further extended.</p>
  </div>
  <div class="pager">&lt; <b>05</b> &gt;</div>
</section>

</body>
</html>
```